Quorva - corporate Business Card

We need a good look and innovative business card for a new start up company based in Los Angeles called "Quorva". We are in a payment business, including payment card, app, and ewallet. We are expert in online payment and Card not present (CNP) transaction.
We need an innovative, modern business card.

Our logo font is Aero Matics

Target Market(s)

Startup - Bank - Online Payment - Card Manufacturing

Industry/Entity Type

Startup

Contact Information for Business Card

phone: 555 014 7396 - Address: 4172 Marlowe blvd, Fenwick Bay, OR 97299

Requirements
Must have
• Message: innovative, professional, expert, high tech, trust, online payment expert, security
Nice to have
• no comment
Should not have
• no Comment

```html
<!DOCTYPE html>
<html lang="en">
<head>
<meta charset="utf-8">
<title>Quorva – Business Card</title>
<link href="https://fonts.googleapis.com/css2?family=Lato:wght@400;700;900&display=swap" rel="stylesheet">
<style>
  :root {
    --brand-red: #b31e2c;
    --brand-red-soft: rgba(255, 255, 255, 0.2);
    --blush: #f1d6da;
    --paper: #ffffff;
    --ink: #1c1c1c;
    --backdrop: #ececec;
  }
  * { box-sizing: border-box; margin: 0; padding: 0; }
  html, body {
    width: 1200px;
    height: 586px;
    overflow: hidden;
    background: var(--backdrop);
    font-family: "Lato", Arial, sans-serif;
  }
  .stage { position: relative; width: 1200px; height: 586px; }

  .card {
    position: absolute;
    top: 129px;
    width: 501px;
    height: 300px;
    overflow: hidden;
  }
  .card--front { left: 61px; background: var(--brand-red); }
  .card--back { left: 619px; background: var(--paper); }

  .card__disc {
    position: absolute;
    width: 260px;
    height: 260px;
    border-radius: 50%;
  }
  .card--front .card__disc { left: 275px; top: 23px; background: var(--brand-red-soft); }
  .card--back .card__disc { left: 285px; top: 89px; background: var(--blush); }

  .wordmark {
    position: absolute;
    font-weight: 700;
    line-height: 1;
    letter-spacing: 0.5px;
  }
  .card--front .wordmark { left: 30px; top: 212px; font-size: 46px; color: var(--paper); }
  .card--back .wordmark {
    left: 0; right: 0; top: 34px;
    text-align: center; font-size: 40px; color: var(--brand-red);
  }

  .web-address {
    position: absolute;
    left: 32px;
    top: 262px;
    font-size: 11.5px;
    font-weight: 700;
    letter-spacing: 3px;
    color: var(--paper);
  }

  .person__name {
    position: absolute; left: 27px; top: 160px;
    font-size: 17px; font-weight: 900; color: var(--brand-red);
  }
  .person__role {
    position: absolute; left: 28px; top: 183px;
    font-size: 11.5px; color: var(--ink);
  }
  .divider {
    position: absolute; left: 0; top: 205px;
    width: 180px; height: 3px;
    background: linear-gradient(90deg, var(--brand-red) 0%, rgba(179, 30, 44, 0.6) 50%, rgba(179, 30, 44, 0) 100%);
  }

  .contact {
    position: absolute; left: 28px;
    display: flex; align-items: center; gap: 8px;
    font-size: 12.5px; color: var(--ink);
  }
  .contact--phone { top: 218px; }
  .contact--email { top: 243px; }
  .contact__icon { width: 18px; height: 18px; flex: none; }

  .postal-address {
    position: absolute; left: 27px; top: 270px;
    font-size: 12.5px; font-weight: 900; color: var(--brand-red);
  }
</style>
</head>
<body>
<main class="stage">

  <section class="card card--front" aria-label="Card front">
    <div class="card__disc"></div>
    <div class="wordmark">quorva</div>
    <div class="web-address">www.quorvapay.com</div>
  </section>

  <section class="card card--back" aria-label="Card back">
    <div class="card__disc"></div>
    <div class="wordmark">quorva</div>

    <div class="person__name">Maren Caldwell</div>
    <div class="person__role">Owner &amp; Founder</div>
    <div class="divider"></div>

    <div class="contact contact--phone">
      <svg class="contact__icon" viewBox="0 0 18 18" aria-hidden="true">
        <circle cx="9" cy="9" r="9" fill="#b31e2c"/>
        <path d="M4.5 7.2c0-1.3 2-2 4.5-2s4.5.7 4.5 2v.8h-2.2v-1H6.7v1H4.5z M5.5 12.8l1.3-4h4.4l1.3 4z" fill="#fff"/>
        <circle cx="9" cy="10.6" r="1" fill="#b31e2c"/>
      </svg>
      <span>(555) 014-7396</span>
    </div>

    <div class="contact contact--email">
      <svg class="contact__icon" viewBox="0 0 18 18" aria-hidden="true">
        <circle cx="9" cy="9" r="9" fill="#b31e2c"/>
        <rect x="4.5" y="5.8" width="9" height="6.4" fill="#fff"/>
        <path d="M4.5 5.8L9 9.4l4.5-3.6" fill="none" stroke="#b31e2c" stroke-width="1"/>
      </svg>
      <span>MarenC@quorvapay.com</span>
    </div>

    <div class="postal-address">4172 Marlowe blvd, Fenwick Bay, OR 97299</div>
  </section>

</main>
</body>
</html>
```